Design logo and business card.

Design and construct logo and card for my business which is an over seeing company of other smaller businesses. The companies name is ember4 business works. Im open to any ideas but i am looking for a very cool contemporary design with a very prestige feel. The card can be either single or double sided, Thank you and i will look forward to your submissions.

Business

• Company name, email, website, telephone, my name. Cool modern look with a prestige feel.

```html
<!DOCTYPE html>
<html lang="en">
<head>
<meta charset="utf-8">
<title>ember4 business works — business card</title>
<link rel="stylesheet" href="https://fonts.googleapis.com/css2?family=Open+Sans:wght@400;600&display=swap">
<style>
  :root {
    --stage: #e4e3e0;
    --card-dark: #1f2122;
    --card-pattern-light: #2c2e30;
    --card-pattern-dark: #1c1d1f;
    --lime: #b8e21f;
    --white: #ffffff;
    --text-font: "Open Sans", Arial, sans-serif;
  }
  * { box-sizing: border-box; margin: 0; padding: 0; }
  html, body { width: 1200px; height: 1000px; overflow: hidden; }
  body { background: var(--stage); position: relative; font-family: var(--text-font); }

  .card {
    position: absolute;
    left: 215px;
    width: 770px;
    height: 440px;
    border-radius: 22px;
    overflow: hidden;
    background: var(--card-dark);
    box-shadow: 0 6px 18px rgba(0,0,0,0.25);
  }
  .card--front { top: 40px; }
  .card--back { top: 520px; }

  .pattern-field {
    position: absolute;
    left: 0; top: 0; width: 100%;
    background: radial-gradient(ellipse at 50% 40%, var(--card-pattern-light), var(--card-pattern-dark));
  }
  .card--front .pattern-field { height: 100%; }
  .card--back .pattern-field { height: 150px; }

  /* front */
  .wordmark {
    position: absolute;
    left: 250px; top: 130px;
    color: var(--lime);
    font-weight: 400;
  }
  .wordmark__name { display: block; font-size: 78px; line-height: 1; letter-spacing: -1px; }
  .wordmark__tag { display: block; font-size: 22px; line-height: 1.2; margin-left: 4px; }

  .url-row {
    position: absolute;
    left: 0; right: 0; top: 340px;
    display: flex;
    align-items: center;
  }
  .accent-bar { height: 13px; background: var(--lime); }
  .accent-bar--front-left { width: 470px; flex: none; }
  .accent-bar--front-right { flex: 1; }
  .website {
    flex: none;
    margin: 0 16px;
    color: var(--white);
    font-size: 22px;
    line-height: 1;
    letter-spacing: 0.3px;
    white-space: nowrap;
  }

  /* back */
  .company-title {
    position: absolute;
    left: 0; top: 88px; width: 100%;
    text-align: center;
    color: var(--white);
    font-size: 34px;
    font-weight: 400;
    letter-spacing: 0.5px;
  }
  .accent-bar--back { position: absolute; left: 0; top: 150px; width: 100%; height: 11px; }
  .contact {
    position: absolute;
    left: 0; top: 215px; width: 100%;
    text-align: center;
    color: var(--white);
  }
  .contact__name { color: var(--lime); font-size: 30px; margin-bottom: 14px; letter-spacing: 0.5px; }
  .contact__line { font-size: 21px; line-height: 1.6; display: flex; justify-content: center; align-items: center; gap: 8px; }
  .contact__icon { width: 16px; height: 16px; }
</style>
</head>
<body>

<section class="card card--front" aria-label="Card front">
  <div class="pattern-field" role="img" aria-label="Dark damask pattern background"></div>
  <div class="wordmark">
    <span class="wordmark__name">ember4</span>
    <span class="wordmark__tag">business works</span>
  </div>
  <div class="url-row">
    <div class="accent-bar accent-bar--front-left"></div>
    <p class="website">www.ember-4.com</p>
    <div class="accent-bar accent-bar--front-right"></div>
  </div>
</section>

<section class="card card--back" aria-label="Card back">
  <div class="pattern-field" role="img" aria-label="Dark damask pattern background"></div>
  <h1 class="company-title">EMBER4 BUSINESS WORKS</h1>
  <div class="accent-bar accent-bar--back"></div>
  <div class="contact">
    <p class="contact__name">NOEL VARGA</p>
    <p class="contact__line">
      <svg class="contact__icon" viewBox="0 0 16 16" aria-hidden="true">
        <rect x="4" y="1" width="8" height="14" rx="1.5" fill="none" stroke="var(--lime)" stroke-width="1.4"/>
        <line x1="7" y1="12.5" x2="9" y2="12.5" stroke="var(--lime)" stroke-width="1.2"/>
      </svg>
      +34 611 420 587
    </p>
    <p class="contact__line">
      <svg class="contact__icon" viewBox="0 0 16 16" aria-hidden="true">
        <rect x="1" y="3.5" width="14" height="9" fill="none" stroke="var(--lime)" stroke-width="1.4"/>
        <polyline points="1,3.5 8,9 15,3.5" fill="none" stroke="var(--lime)" stroke-width="1.4"/>
      </svg>
      info@ember-4.com
    </p>
  </div>
</section>

</body>
</html>
```